Premium Food Label Design – High-End Boutique Jar Labels (3 Sizes)

I require a complete jar label redesign across three sizes:
75mm x 130mm (Large & Medium)
55mm x 120mm (Small)
45mm x 120mm (XS)

The design must feel professional, modern, elegant, and high-end boutique.
Primary aesthetic: white, minimal, refined, with accents in soft brown and gold/bronze. (see prefer colours of logo in OLD LABEL PDF)
Transparent background required.

I have attached my current label for wording reference only — I want to move away from the kraft look entirely.
The label must include all existing details, plus a dedicated space to manually add batch number and date.

IMPORTANT: Final files must be supplied as editable Adobe Illustrator (.AI) files with live text layers (not outlined) so I can update them as needed.
Logo is attached. I’m open to a fresh, elevated design direction aligned with a premium brand feel.

Target Market(s)

People who appreciate high-end, thoughtfully crafted food and are willing to pay for quality

Industry/Entity Type

Gourmet Food / Artisan Food Packaging

Requirements
Must have
• Premium, minimal aesthetic, Strong typography hierarchy, White background, Consistency across 3 sizes
Nice to have
• Elevated “Tide Lantern” styling
Should not have
• No bright or bold colours, No clutter or overcrowding, No heavy borders or thick frames,No “homemade/craft” fonts

```html
<!DOCTYPE html>
<html lang="en">
<head>
<meta charset="utf-8">
<title>Tomato Relish Labels – Three Sizes</title>
<link href="https://fonts.googleapis.com/css2?family=Josefin+Sans:wght@300;400;600&family=Jost:wght@400;500;600&family=Libre+Baskerville:ital@1&display=swap" rel="stylesheet">
<style>
  :root{
    --page:#ffffff;
    --cream:#f7f3e4;
    --ribbon:#3e2516;
    --copper:#b0672f;
    --copper-light:#d08a52;
    --band-dark:#8b3c16;
    --band-mid:#b4602c;
    --ink:#3a2516;
    --gold:#b48a5a;
    --band-text:#f7ead6;
  }
  *{box-sizing:border-box;margin:0;padding:0}
  html,body{width:1200px;height:1200px;overflow:hidden;background:var(--page)}
  body{font-family:"Jost",sans-serif;color:var(--ink)}
  .label-row{
    position:absolute;left:0;top:0;width:1200px;height:1200px;
    display:flex;align-items:center;justify-content:center;gap:28px;padding:0 26px;
  }
  .label{
    width:370px;background:var(--cream);border-radius:4px;
    display:flex;flex-direction:column;overflow:hidden;
    box-shadow:0 0 0 1px rgba(62,37,22,.08);
  }
  .label--large{height:214px;font-size:9.6px}
  .label--medium{height:170px;font-size:8.6px}
  .label--small{height:140px;font-size:7.4px}

  .label__top{flex:48;position:relative;display:flex}
  .label__ribbon{position:absolute;left:16%;top:0;width:27%;height:100%}
  .label__ribbon svg{position:absolute;inset:0;width:100%;height:100%}
  .brand-name{
    position:absolute;left:0;right:0;top:32%;text-align:center;
    font-family:"Josefin Sans",sans-serif;font-weight:400;color:var(--copper-light);
    font-size:1.35em;letter-spacing:.12em;line-height:1.15;
  }
  .label__intention{
    position:absolute;left:52%;right:3%;top:10%;text-align:center;line-height:1.5;font-size:.9em;
  }
  .label__intention h3{font-weight:600;font-size:1em;margin-bottom:.25em}

  .label__band{
    flex:19;display:flex;align-items:center;
    background:linear-gradient(90deg,var(--band-dark) 0%,var(--band-mid) 55%,var(--band-dark) 100%);
    color:var(--band-text);
  }
  .product-name{
    width:50%;text-align:center;font-family:"Josefin Sans",sans-serif;font-weight:400;
    font-size:2.1em;letter-spacing:.04em;color:#f3e1c8;
  }
  .ingredients{width:50%;text-align:center;font-size:.85em;line-height:1.35;padding-right:2%}
  .ingredients strong{display:block;font-weight:500;color:#f8e3b8}

  .label__bottom{flex:33;display:flex;align-items:center}
  .variant{width:46%;text-align:center}
  .variant__name{
    display:inline-block;font-family:"Josefin Sans",sans-serif;font-size:1.2em;
    border-bottom:1px solid var(--ink);padding:0 .2em .1em;letter-spacing:.03em;
  }
  .variant__tag{font-family:"Libre Baskerville",serif;font-style:italic;color:var(--gold);font-size:.95em;margin:.2em 0 .5em}
  .variant__weight{font-size:1.1em;font-weight:500}
  .details{width:54%;text-align:center;font-size:.72em;line-height:1.5;padding-right:2%}
  .details__storage{font-weight:600;margin-bottom:.7em}
  .details__record{display:flex;justify-content:center;gap:1.2em;margin-bottom:.9em}
  .details__record span{display:inline-block;width:7em;border-bottom:1px solid var(--ink);vertical-align:baseline}
  .details__maker{font-weight:600}
</style>
</head>
<body>
<main class="label-row">

  <article class="label label--large">
    <section class="label__top">
      <div class="label__ribbon">
        <svg viewBox="0 0 100 100" preserveAspectRatio="none" aria-hidden="true"><polygon points="0,0 100,0 100,100 50,84 0,100" fill="#3e2516"/></svg>
        <div class="brand-name">EMBER<br>PANTRY</div>
      </div>
      <div class="label__intention">
        <h3>Tide Lantern</h3>
        <p>What is made with love is felt in return. May this Relish nourish more than the meal - bringing comfort, connection and joy to every moment shared.</p>
      </div>
    </section>
    <section class="label__band">
      <h2 class="product-name">TOMATO RELISH</h2>
      <p class="ingredients"><strong>Ingredients:</strong>Tomatoes, Onion, Sugar, Vinegar, Salt, Spices, &amp; Thickener (Cornflour)</p>
    </section>
    <section class="label__bottom">
      <div class="variant">
        <p class="variant__name">POPULAR CHOICE</p>
        <p class="variant__tag">Made with Love</p>
        <p class="variant__weight">375g</p>
      </div>
      <div class="details">
        <p class="details__storage">STORAGE: KEEP REFRIGERATED ONCE OPENED!</p>
        <p class="details__record"><em style="font-style:normal">Batch: # <span></span></em><em style="font-style:normal">Date: # <span></span></em></p>
        <p class="details__maker">Made by: Ember Pantry, QLD, Australia</p>
        <p class="details__maker">www.emberpantry.com | info@emberpantry.com</p>
      </div>
    </section>
  </article>

  <article class="label label--medium">
    <section class="label__top">
      <div class="label__ribbon">
        <svg viewBox="0 0 100 100" preserveAspectRatio="none" aria-hidden="true"><polygon points="0,0 100,0 100,100 50,84 0,100" fill="#3e2516"/></svg>
        <div class="brand-name">EMBER<br>PANTRY</div>
      </div>
      <div class="label__intention">
        <h3>Tide Lantern</h3>
        <p>What is made with love is felt in return. May this Relish nourish more than the meal - bringing comfort, connection and joy to every moment shared.</p>
      </div>
    </section>
    <section class="label__band">
      <h2 class="product-name">TOMATO RELISH</h2>
      <p class="ingredients"><strong>Ingredients:</strong>Tomatoes, Onion, Sugar, Vinegar, Salt, Spices, &amp; Thickener (Cornflour)</p>
    </section>
    <section class="label__bottom">
      <div class="variant">
        <p class="variant__name">POPULAR CHOICE</p>
        <p class="variant__tag">Made with Love</p>
        <p class="variant__weight">375g</p>
      </div>
      <div class="details">
        <p class="details__storage">STORAGE: KEEP REFRIGERATED ONCE OPENED!</p>
        <p class="details__record"><em style="font-style:normal">Batch: # <span></span></em><em style="font-style:normal">Date: # <span></span></em></p>
        <p class="details__maker">Made by: Ember Pantry, QLD, Australia</p>
        <p class="details__maker">www.emberpantry.com | info@emberpantry.com</p>
      </div>
    </section>
  </article>

  <article class="label label--small">
    <section class="label__top">
      <div class="label__ribbon">
        <svg viewBox="0 0 100 100" preserveAspectRatio="none" aria-hidden="true"><polygon points="0,0 100,0 100,100 50,84 0,100" fill="#3e2516"/></svg>
        <div class="brand-name">EMBER<br>PANTRY</div>
      </div>
      <div class="label__intention">
        <h3>Tide Lantern</h3>
        <p>What is made with love is felt in return. May this Relish nourish more than the meal - bringing comfort, connection and joy to every moment shared.</p>
      </div>
    </section>
    <section class="label__band">
      <h2 class="product-name">TOMATO RELISH</h2>
      <p class="ingredients"><strong>Ingredients:</strong>Tomatoes, Onion, Sugar, Vinegar, Salt, Spices, &amp; Thickener (Cornflour)</p>
    </section>
    <section class="label__bottom">
      <div class="variant">
        <p class="variant__name">POPULAR CHOICE</p>
        <p class="variant__tag">Made with Love</p>
        <p class="variant__weight">375g</p>
      </div>
      <div class="details">
        <p class="details__storage">STORAGE: KEEP REFRIGERATED ONCE OPENED!</p>
        <p class="details__record"><em style="font-style:normal">Batch: # <span></span></em><em style="font-style:normal">Date: # <span></span></em></p>
        <p class="details__maker">Made by: Ember Pantry, QLD, Australia</p>
        <p class="details__maker">www.emberpantry.com | info@emberpantry.com</p>
      </div>
    </section>
  </article>

</main>
</body>
</html>
```